Marlowe Group needs a business card

I would like the card to be simple but modern and elegant.
I like black and white.
or black and gold.
we are a private finance lender and also are involved in property and property developments.

please look at the business card photos i provided i would like M.G only one one side and all the other details on the other side use fonts that tie in with my theme.

Industry/Entity Type

Finance

Contact Information for Business Card

Marlowe Group (M.G) Daniel Marlowe M: 0413586207 E: danmarl@inboxmail.test

Font styles to use
Other font styles liked:
• Use fonts that would reflect our business

Colors
000000
ffffff

Requirements
Must have
• one side of details
• other side has either M.G or Marlowe Group like in the photos provided

```html
<!DOCTYPE html>
<html lang="en">
<head>
<meta charset="utf-8">
<title>Marlowe Group — Business Card</title>
<link rel="stylesheet" href="https://fonts.googleapis.com/css2?family=Marcellus+SC&family=Montserrat:wght@600&family=Open+Sans:wght@400&display=swap">
<style>
  :root {
    --stage: #262626;
    --card: #050505;
    --ink: #ffffff;
    --ink-soft: #e6e6e6;
  }
  * { margin: 0; padding: 0; box-sizing: border-box; }
  html, body {
    width: 1200px;
    height: 900px;
    overflow: hidden;
    background: var(--stage);
  }
  .canvas {
    position: relative;
    width: 1200px;
    height: 900px;
  }
  .card {
    position: absolute;
    left: 320px;
    width: 560px;
    height: 320px;
    background: var(--card);
    box-shadow: 0 10px 30px rgba(0, 0, 0, 0.45);
  }
  .card--front { top: 100px; }
  .card--back { top: 480px; }

  /* Front: company name breaking a hairline rule */
  .brand-rule {
    position: absolute;
    left: 0;
    right: 0;
    top: 160px;
    display: flex;
    align-items: center;
    gap: 14px;
  }
  .brand-rule__line {
    flex: 1;
    height: 1px;
    background: var(--ink-soft);
  }
  .brand-rule__line--left { flex: 0 0 150px; }
  .brand-name {
    font-family: "Marcellus SC", serif;
    font-size: 30px;
    letter-spacing: 1px;
    color: var(--ink);
    white-space: nowrap;
    line-height: 1;
    transform: translateY(-4px);
  }

  /* Back: name, divider, contact details */
  .details {
    position: absolute;
    left: 120px;
    top: 150px;
    display: flex;
    align-items: center;
    gap: 12px;
  }
  .details__name {
    font-family: "Montserrat", sans-serif;
    font-weight: 600;
    font-size: 16px;
    letter-spacing: 0.5px;
    color: var(--ink);
    text-transform: uppercase;
    white-space: nowrap;
  }
  .details__divider {
    width: 1px;
    height: 38px;
    background: var(--ink);
  }
  .details__contact {
    font-family: "Open Sans", sans-serif;
    font-size: 12px;
    line-height: 18px;
    color: var(--ink);
    letter-spacing: 0.6px;
    list-style: none;
  }
  .details__label { margin-right: 6px; }
</style>
</head>
<body>
  <main class="canvas">
    <section class="card card--front" aria-label="Card front">
      <div class="brand-rule">
        <span class="brand-rule__line brand-rule__line--left"></span>
        <h1 class="brand-name">Marlowe Group</h1>
        <span class="brand-rule__line"></span>
      </div>
    </section>

    <section class="card card--back" aria-label="Card back">
      <div class="details">
        <h2 class="details__name">Daniel Marlowe</h2>
        <span class="details__divider"></span>
        <ul class="details__contact">
          <li><span class="details__label">M:</span>041. 358. 6207</li>
          <li><span class="details__label">E:</span>danmarl@inboxmail.test</li>
        </ul>
      </div>
    </section>
  </main>
</body>
</html>
```